A 'new law' boutique Australian law firm that provides specialist employment law and people managem

We value helping clients create results with respect workplaces. What differentiates us is we provide actionable training in understanding and dealing with people and ensure legal compliance fits with this approach. We would like a fresh approach to our training overview documents that we currently use in our current law firm (6 attached). Please use pictures, symbols etc consistent with our non-traditional law approach that captures the approach of each training session.. Attached is the logo and draft letterhead for Birchwell Legal which will launch soon.

Target Market(s)

HR Managers and in-house lawyers (non employment specialists) in mid-large Australian companies that are progressive with a relationship based approach to managing employee behaviours and disputes.

Industry/Entity Type

Human Resource

Font styles to use
Sans Serif

Colors
3176b5
33a6d7

Requirements
Must have
• 1 or 2 page PDF for each of the 6 documents that the wording supplied goes into your design which will be pretty similar as we want consistency with our documents

```html
<!DOCTYPE html>
<html lang="en">
<head>
<meta charset="utf-8">
<title>Managing Fitness For Work (Capacity) – Birchwell Legal</title>
<link href="https://fonts.googleapis.com/css2?family=Open+Sans:wght@300;400;600;700&display=swap" rel="stylesheet">
<style>
  :root{
    --brand-blue:#3176b5;
    --brand-sky:#33a6d7;
    --band-blue:#1f78c1;
    --panel-dark:#2b2b2d;
    --col-top:#4dbfeb;
    --col-mid:#73cbef;
    --col-low:#dcedf8;
    --heading-blue:#1f7ab8;
    --title-accent:#7cc8ef;
    --ink:#333;
    --ink-dark:#2a2a2a;
    --white:#fff;
    --ring-grey:#6f6f70;
    --icon-fill:#5cc0ea;
  }
  *{margin:0;padding:0;box-sizing:border-box}
  html,body{width:848px;height:1200px;overflow:hidden;background:#fff}
  body{font-family:"Open Sans",sans-serif;color:var(--ink)}
  .sheet{position:relative;width:848px;height:1200px;overflow:hidden;background:#fff}
  .shapes{position:absolute;inset:0}

  .brand{position:absolute;left:30px;top:84px}
  .brand-name{font-size:18px;font-weight:700;color:var(--brand-blue);letter-spacing:.3px;display:flex;align-items:center;gap:7px;white-space:nowrap}
  .brand-dot{width:11px;height:11px;border-radius:50%;background:var(--brand-blue);flex:none}

  .contact{position:absolute;left:305px;top:65px;color:var(--white);font-size:12.2px;font-weight:400;line-height:20px}
  .contact li{list-style:none;display:flex;align-items:center;gap:7px;white-space:nowrap}
  .contact svg{width:13px;height:13px;flex:none}

  .title{position:absolute;right:392px;top:216px;text-align:right;color:var(--white);font-weight:700;font-size:36px;line-height:43px}
  .title .accent{color:var(--title-accent)}
  .need{position:absolute;right:392px;top:334px;color:var(--brand-sky);font-size:20px;font-weight:600}
  .need-copy{position:absolute;left:70px;width:386px;top:378px;text-align:right;color:var(--white);font-weight:300;font-size:12px;line-height:19px}
  .need-copy p{margin-bottom:8.5px}

  .outcomes{position:absolute;left:60px;top:880px;width:425px}
  .outcomes h2{color:var(--heading-blue);font-size:20px;font-weight:600;margin-bottom:5px}
  .outcomes .lead{font-size:11.3px;font-weight:600;color:var(--ink-dark);line-height:15px;margin-bottom:4px}
  .outcomes ol{padding-left:14px;font-size:11.3px;font-weight:400;color:var(--ink-dark);line-height:15px}
  .outcomes li{margin-bottom:3px;padding-left:2px}

  .overview{position:absolute;left:545px;width:270px}
  .overview h2{font-size:19px;font-weight:600;color:var(--heading-blue)}
  .overview h3{font-size:15px;font-weight:600;color:var(--ink-dark);line-height:20.5px}
  .bullets{list-style:none;color:var(--white);font-weight:400;font-size:11.8px;line-height:16.5px}
  .bullets li{position:relative;padding-left:9px;margin-bottom:8px}
  .bullets li::before{content:"•";position:absolute;left:0;top:0}
  .bullets.tight li{margin-bottom:7.5px}
  .bullets .hl{color:var(--brand-sky)}
  .bullets.dark{color:var(--ink-dark)}

  .ov-1{top:52px}
  .ov-1 h3{margin-top:16px;margin-bottom:14px}
  .ov-2{top:405px}
  .ov-2 h3+h3{margin-top:9px}
  .ov-2 .bullets{margin-top:14px}
  .ov-3{top:1089px}
  .ov-3 h3{margin-bottom:6px}
</style>
</head>
<body>
<div class="sheet">
  <svg class="shapes" width="848" height="1200" viewBox="0 0 848 1200" aria-hidden="true">
    <polygon points="174,0 505,0 505,117 262,117" fill="var(--band-blue)"/>
    <polygon points="0,129 466,129 505,176 505,823 0,823" fill="var(--panel-dark)"/>
    <polygon points="0,780 0,823 38,823" fill="#fff"/>
    <polygon points="505,0 848,0 848,379 543,379 505,334" fill="var(--col-top)"/>
    <polygon points="505,379 848,379 848,1069 543,1069 505,1026" fill="var(--col-mid)"/>
    <polygon points="505,1069 848,1069 848,1200 543,1200 505,1157" fill="var(--col-low)"/>
    <circle cx="150" cy="823" r="69" fill="#fff"/>
    <circle cx="150" cy="823" r="57" fill="var(--icon-fill)" stroke="var(--ring-grey)" stroke-width="5"/>
    <g fill="#fff">
      <rect x="106" y="808" width="7" height="30" rx="3"/>
      <rect x="116" y="799" width="12" height="48" rx="5"/>
      <rect x="128" y="819" width="44" height="8"/>
      <rect x="172" y="799" width="12" height="48" rx="5"/>
      <rect x="187" y="808" width="7" height="30" rx="3"/>
    </g>
  </svg>

  <div class="brand"><span class="brand-name"><span class="brand-dot"></span>BIRCHWELL LEGAL</span></div>

  <ul class="contact">
    <li><svg viewBox="0 0 14 14"><circle cx="7" cy="7" r="6.5" fill="#fff"/><path d="M1 7h12M7 1c-2.5 3-2.5 9 0 12M7 1c2.5 3 2.5 9 0 12" stroke="var(--band-blue)" fill="none" stroke-width="1"/></svg>www.birchwelllegal.com.au</li>
    <li><svg viewBox="0 0 14 14"><circle cx="7" cy="7" r="6.5" fill="#fff"/><rect x="3.5" y="4.5" width="7" height="5" fill="none" stroke="var(--band-blue)"/><path d="M3.5 4.5 7 7.5l3.5-3" fill="none" stroke="var(--band-blue)"/></svg>info@birchwelllegal.com.au</li>
  </ul>

  <h1 class="title">Managing Fitness<br>For Work <span class="accent">(Capacity)</span></h1>
  <h2 class="need">Training Need</h2>
  <div class="need-copy">
    <p>Too often performance and behavioural issues are interrelated with mental health issues or the effects of injuries and other medical conditions (whether work related or not). This may mean an employee ‘can’t’ perform to the expected standard rather than they ‘won’t’.</p>
    <p>Because this is a highly regulated area, processes can become complex quickly. This is particularly so with mental health in the workplace which is a ‘hot topic’ and a complex issue to manage from a legal and practical perspective.</p>
    <p>Increased awareness of mental health issues has increased our understanding that performance and mental health issues are often interrelated and cannot be managed in isolation. This has led to a more proactive approach to dealing with mental health issues in the workplace with serious legal consequences for organisations that adopt the old thinking of ‘don’t ask - don’t tell’.</p>
    <p>However, the new challenge is how to manage privacy concerns, the need for medical evidence and how to provide reasonable adjustments without dropping performance standards.</p>
  </div>

  <section class="outcomes">
    <h2>Learning Outcomes</h2>
    <p class="lead">This workshop enables HR to assist managers to deal with fitness for work (physical and mental) to:</p>
    <ol>
      <li>manage the tension supporting employees with health issues and ensuring effective performance;</li>
      <li>know when and how to adopt an effective Fitness for Work Procedure rather than traditional Performance Improvement Plans where health issues impact on performance;</li>
      <li>manage long term absence, suspected personal leave abuse, associated workers compensation claims and ‘push back’ with fitness for work concerns, obtaining medical evidence and return to work requirements;</li>
      <li>deal with subjective perceptions of bullying that are connected to mental health issues where there is no objective bullying; and</li>
      <li>implement the right process to decide facts and determine outcomes using reasonable response action options</li>
    </ol>
  </section>

  <section class="overview ov-1">
    <h2>Training Overview</h2>
    <h3>Understanding Capacity<br>as a workplace issue</h3>
    <ul class="bullets">
      <li>What is mental illness and what is wrong with the current approach</li>
      <li>Symptoms and effects of Depression and Anxiety in the workplace</li>
      <li>Separating a disability (physical and mental) from its symptoms and effects</li>
      <li>Relevant legal framework and commonly arising legal claims such as unfair dismissal, adverse action, discrimination, bullying and stress claims, and workers compensation</li>
    </ul>
  </section>

  <section class="overview ov-2">
    <h3>3 Step approach to dealing with Capacity (Fitness for Work) issues: Assess Risk, Determine Facts and Decide Outcomes</h3>
    <h3>Using a Response Action Plan to implement the 3 Step approach</h3>
    <ul class="bullets tight">
      <li><span class="hl">WH&amp;S Approach</span> to assessing relevant risk</li>
      <li>Risk and Protective factors at work</li>
      <li>Classifying behaviours and issues into a legal framework of Performance, Conduct (Disciplinary) and Capacity (Fitness for Work) or a combination and the differences</li>
      <li>How to determine the inherent requirements of a position (physical and mental)</li>
      <li>How to seek medical advice and options when an employee is resisting</li>
      <li>Dealing with conflicting medical opinions</li>
      <li>Treating health care professionals v medico-legal assessments</li>
      <li>Requiring medical certificates and dealing with lack of co-operation</li>
      <li>Difference between Temporary and</li>
      <li>Permanent Incapacity</li>
      <li>How to provide reasonable adjustments, return to work plans, redeployment, reasonable management action and exit employees as response action</li>
      <li>Workers compensation considerations</li>
    </ul>
  </section>

  <section class="overview ov-3">
    <h3>Examples of scenarios</h3>
    <ul class="bullets dark">
      <li>Practice by applying the 3 steps to case studies and actual previous issues dealt with and considering different outcomes</li>
    </ul>
  </section>
</div>
</body>
</html>
```